Simple and Clean business card design

We would like the design to be simple clean and to incorporate our colors.

We are open to your design and talent, we have the dots in our logo as we think of it as data points and we connect data points for people.

We are open to see the great creative and clean design you bring to the table

Contact Information for Business Card

please include: name, position, email, phone and website

Font styles to use
Sans Serif

Requirements
Must have
• my colors incorporated, simplicity
Nice to have
• lots of white space, simplicity
Should not have
• complexicity/ complex art

```html
<!DOCTYPE html>
<html lang="en">
<head>
<meta charset="UTF-8">
<title>Tessel — Business Card</title>
<link href="https://fonts.googleapis.com/css2?family=Montserrat:wght@400;500;700&display=swap" rel="stylesheet">
<style>
  :root {
    --backdrop: #3b3835;
    --card: #1c1d1f;
    --ink: #ffffff;
    --muted: #e6e6e6;
    --green: #34a853;
    --yellow: #fbbc05;
    --red: #ea4335;
    --blue: #4a7bc8;
    --faint: #2a2b2d;
  }
  * { margin: 0; padding: 0; box-sizing: border-box; }
  html, body { width: 1200px; height: 900px; overflow: hidden; }
  body {
    background: var(--backdrop);
    font-family: "Montserrat", sans-serif;
    display: flex;
    flex-direction: column;
    align-items: center;
    justify-content: center;
    gap: 40px;
  }
  .card {
    width: 700px;
    height: 400px;
    background: var(--card);
    position: relative;
    overflow: hidden;
    box-shadow: 0 10px 30px rgba(0,0,0,0.35);
  }
  /* Back side */
  .card--back .faint-disc {
    position: absolute;
    left: 40px;
    top: 170px;
    width: 300px;
    height: 300px;
    border-radius: 50%;
    background: var(--faint);
  }
  .card--back .brand {
    position: absolute;
    right: 60px;
    top: 150px;
    font-size: 58px;
  }
  /* Shared brand wordmark */
  .brand {
    display: flex;
    align-items: center;
    gap: 14px;
    color: var(--ink);
    font-weight: 700;
    letter-spacing: 1px;
    line-height: 1;
  }
  .brand__dot {
    width: 0.42em;
    height: 0.42em;
    border-radius: 50%;
    background: var(--green);
    flex: none;
  }
  /* Front side */
  .card--front {
    display: flex;
    align-items: center;
  }
  .card--front .brand {
    font-size: 72px;
    width: 395px;
    justify-content: center;
  }
  .divider {
    width: 2px;
    height: 230px;
    background: var(--muted);
    flex: none;
  }
  .details {
    padding-left: 32px;
    color: var(--ink);
  }
  .person__name {
    font-size: 22px;
    font-weight: 700;
    letter-spacing: 1px;
    text-transform: uppercase;
  }
  .person__first { color: var(--green); }
  .person__role {
    font-size: 17px;
    font-weight: 500;
    margin-top: 4px;
  }
  .address {
    font-style: normal;
    font-size: 14px;
    line-height: 1.35;
    margin-top: 20px;
  }
  .contact-list {
    list-style: none;
    margin-top: 20px;
    font-size: 14px;
  }
  .contact-list li {
    display: flex;
    align-items: center;
    gap: 10px;
    margin-bottom: 6px;
  }
  .contact-list svg {
    width: 14px;
    height: 14px;
    fill: var(--green);
    flex: none;
  }
</style>
</head>
<body>

  <section class="card card--back" aria-label="Card back">
    <div class="faint-disc"></div>
    <div class="brand"><span class="brand__dot"></span>tessel</div>
  </section>

  <section class="card card--front" aria-label="Card front">
    <div class="brand"><span class="brand__dot"></span>tessel</div>
    <div class="divider"></div>
    <div class="details">
      <p class="person__name"><span class="person__first">Marcus</span> Delaney</p>
      <p class="person__role">Founder/ CEO</p>
      <address class="address">218 W. Oak Avenue<br>Riverton, IL 60412</address>
      <ul class="contact-list">
        <li>
          <svg viewBox="0 0 24 24" aria-hidden="true"><path d="M6.6 10.8a15.1 15.1 0 0 0 6.6 6.6l2.2-2.2c.3-.3.7-.4 1-.2 1.1.4 2.3.6 3.6.6.6 0 1 .4 1 1V20c0 .6-.4 1-1 1A17 17 0 0 1 3 4c0-.6.4-1 1-1h3.5c.6 0 1 .4 1 1 0 1.3.2 2.5.6 3.6.1.3 0 .7-.2 1z"/></svg>
          555-214-3098
        </li>
        <li>
          <svg viewBox="0 0 24 24" aria-hidden="true"><path d="M2 5h20v14H2z M4 7v.4l8 5 8-5V7l-8 5z" fill-rule="evenodd"/></svg>
          m.delaney@tessel.one
        </li>
        <li>
          <svg viewBox="0 0 24 24" aria-hidden="true"><circle cx="12" cy="12" r="10"/></svg>
          www.tessel.one
        </li>
      </ul>
    </div>
  </section>

</body>
</html>
```